Local massage therapist needs some new marketing material

Hi there! I am a massage therapist here in Denver, CO in Alder Bend(shopping and art district) of the city. My business is called Lumo Bodywork of Denver. My practice has an eastern influence and I do reflexology, thai massage and use Chinese herbs, etc. I know all my clients and pay close attention to details. I am also very respectful of tradition and it shows in how I work. I tend to like modern, clean, fun, Asian designs. I am wanting a new business card and brochure. I have a logo and branding for my business that I want used in the design. Currently, the sign for my building is purple and I think my logo was designed to be purple. I will attach pictures of it and can send whatever files are necessary so it can be integrated into the brochure, etc. I like the purple but open to using other colors as well. Thanks!
My website is lumobodyworkofdenver.example where info can be gathered about me and services/fees for brochure.
Updates

Just increased budget. Please see new feedback in discussion thread.

Thanks!

                                       HEY ALL,

Just wanted to let you know that I made a change to my website. It is on the Prices Page. I no longer have the frequent  flyer prices but I added discounts. Let me know if you have any questions. Thanks so much!

Target Market(s)

healthy, urban, educated, upper middle class, yogis

Industry/Entity Type

Marketing

Requirements
Must have
• logo stays purple
Should not have
• not too busy

```html
<!DOCTYPE html>
<html lang="en">
<head>
<meta charset="utf-8">
<title>Lumo Bodywork of Denver – Business Card</title>
<link rel="stylesheet" href="https://fonts.googleapis.com/css2?family=Open+Sans:ital,wght@0,300;0,400;0,600;0,700;1,400&display=swap">
<style>
  :root {
    --purple: #6a2c91;
    --charcoal: #3a3a3c;
    --ink: #4a4a4a;
    --muted: #7a7a7a;
    --rule: #9a9a9a;
    --card: #ffffff;
    --backdrop: #e6e6ea;
  }
  * { box-sizing: border-box; margin: 0; padding: 0; }
  html, body { width: 1200px; height: 987px; overflow: hidden; }
  body {
    background: var(--backdrop);
    font-family: "Open Sans", Arial, sans-serif;
    color: var(--ink);
    position: relative;
  }
  .card {
    position: absolute;
    width: 740px;
    height: 423px;
    background: var(--card);
    border-radius: 34px;
    overflow: hidden;
    box-shadow: 0 6px 18px rgba(0,0,0,0.12);
  }
  .card--back { left: 400px; top: 50px; }
  .card--front { left: 60px; top: 510px; }

  /* brand lockup */
  .brand { display: flex; align-items: center; gap: 16px; color: var(--purple); }
  .brand__dot { width: 46px; height: 46px; border-radius: 50%; background: var(--purple); }
  .brand__name { font-weight: 400; font-size: 64px; letter-spacing: 8px; line-height: 1; }

  /* front */
  .front__wave { position: absolute; left: 0; bottom: 0; width: 740px; height: 423px; }
  .front__brand { position: absolute; left: 0; right: 0; top: 60px; justify-content: center; }
  .identity {
    position: absolute; right: 410px; top: 180px; text-align: right;
  }
  .identity__name { color: var(--purple); font-weight: 700; font-size: 25px; line-height: 1.2; }
  .identity__title, .identity__address { font-size: 17px; line-height: 1.35; color: var(--ink); }
  .front__divider {
    position: absolute; left: 345px; top: 180px; width: 1px; height: 118px; background: var(--rule);
  }
  .contact { position: absolute; left: 362px; top: 186px; list-style: none; }
  .contact__item { display: flex; align-items: center; gap: 9px; font-size: 18px; line-height: 1.75; color: var(--ink); }
  .contact__icon { width: 17px; height: 17px; flex: none; }

  /* back */
  .appointment { position: absolute; left: 48px; top: 40px; width: 640px; }
  .appointment__heading { color: var(--purple); font-weight: 700; font-size: 17px; letter-spacing: 0.5px; margin-bottom: 16px; }
  .field { display: flex; align-items: flex-end; font-size: 17px; height: 34px; }
  .field__line { border-bottom: 1px dotted var(--rule); height: 1px; margin: 0 8px 5px; }
  .appointment__hours { font-size: 17px; line-height: 1.45; margin-top: 14px; }
  .appointment__note { font-style: italic; color: var(--muted); font-size: 16px; margin-top: 4px; }
  .back__brand { position: absolute; right: 44px; bottom: 44px; }
  .back__brand .brand__name { font-size: 52px; }
  .back__brand .brand__dot { width: 38px; height: 38px; }
</style>
</head>
<body>

  <section class="card card--back" aria-label="Appointment card, back">
    <div class="appointment">
      <h2 class="appointment__heading">YOUR APPOINTMENT</h2>
      <div class="field"><span>Name :</span><span class="field__line" style="width:520px"></span></div>
      <div class="field"><span>Date :</span><span class="field__line" style="width:200px"></span><span>Time :</span><span class="field__line" style="width:180px"></span><span>am / pm</span></div>
      <p class="appointment__hours">Tues - Fri 10am - 8pm Sat 10am-5pm<br>(Appointments required) No walk-ins please.</p>
      <p class="appointment__note">We appreciate a 24 hr. notice for cancellations</p>
    </div>
    <div class="brand back__brand">
      <span class="brand__dot"></span>
      <span class="brand__name">LUMO</span>
    </div>
  </section>

  <section class="card card--front" aria-label="Business card, front">
    <svg class="front__wave" viewBox="0 0 740 423" aria-hidden="true">
      <path d="M0,272 C130,300 260,345 410,385 C530,415 640,423 740,423 L0,423Z" fill="var(--charcoal)"/>
      <path d="M0,292 C140,322 270,368 430,402 C540,421 640,423 700,423 L0,423Z" fill="#ffffff"/>
      <path d="M0,300 C140,330 270,374 430,406 C530,421 620,423 680,423 L0,423Z" fill="var(--purple)"/>
    </svg>

    <div class="brand front__brand">
      <span class="brand__dot"></span>
      <span class="brand__name">LUMO</span>
    </div>

    <div class="identity">
      <p class="identity__name">Your Name</p>
      <p class="identity__title">Title</p>
      <p class="identity__address">1148 E Larkspur Ave, Denver<br>CO 80299</p>
    </div>
    <div class="front__divider"></div>

    <ul class="contact">
      <li class="contact__item">
        <svg class="contact__icon" viewBox="0 0 20 20" aria-hidden="true"><circle cx="10" cy="10" r="10" fill="var(--purple)"/><path d="M7 5l2 3-1.2 1.2c.6 1.3 1.6 2.3 2.9 2.9L12 11l3 2-1 2c-4 0-8-4-8-8z" fill="#fff"/></svg>
        303.555.0142
      </li>
      <li class="contact__item">
        <svg class="contact__icon" viewBox="0 0 20 20" aria-hidden="true"><circle cx="10" cy="10" r="10" fill="var(--purple)"/><rect x="5" y="6.5" width="10" height="7" fill="#fff"/><path d="M5 6.5l5 4 5-4" fill="none" stroke="var(--purple)" stroke-width="1.2"/></svg>
        info@lumobodyworkofdenver.example
      </li>
      <li class="contact__item">
        <svg class="contact__icon" viewBox="0 0 20 20" aria-hidden="true"><circle cx="10" cy="10" r="10" fill="var(--purple)"/><g fill="none" stroke="#fff" stroke-width="1.1"><circle cx="10" cy="10" r="5.5"/><ellipse cx="10" cy="10" rx="2.5" ry="5.5"/><path d="M4.5 10h11"/></g></svg>
        www.lumobodyworkofdenver.example
      </li>
    </ul>
  </section>

</body>
</html>
```